Business card design for holistic health care clinic

We need a double-sided business card design for our holistic health care clinic that integrates our logo design and also its color scheme. My business is called Valmira. It is an integrative medicine clinic. You have already done the logo for me. Please ensure an elegant and upscale design that is not cluttered, but still has all the necessary information (please see below for details).

Target Market(s)

Wellness, fitness, rehabilitation for educated, well-traveled open-minded clients who are focused on natural, organic, balanced and preventive healthcare and lifestyle.

Industry/Entity Type

Medical

Contact Information for Business Card

Modern, clean.

Number of Pages Required

1 page

Font styles to use
Serif
Sans Serif

Colors

Designer to choose colors to be used in the design.

Requirements
Must have
• Logo on one side, all other information on the other side.
• Other information should include:
• Tobias Wrenfeld - DOE, CPT, LMT
• 4100 East Marrow Drive
• Austin, TX 78119
• 512 555 0148
• 818 555 0192
• info@ValmiraHealth.example
• t.wrenfeld@ValmiraHealth.example
Nice to have
• Darker background on front - but not totally black - shaded/dark gray.

```html
<!DOCTYPE html>
<html lang="en">
<head>
<meta charset="utf-8">
<title>Valmira – Business Card</title>
<link rel="stylesheet" href="https://fonts.googleapis.com/css2?family=Roboto:ital,wght@0,400;0,700;0,900;1,500&family=Roboto+Condensed:wght@700&display=swap">
<style>
  :root {
    --brand-blue: #0a8ac6;
    --ink: #444444;
    --rule: #8a8a8a;
    --band-grey: #a9a9a9;
    --card-white: #f4f4f4;
    --card-dark: #262626;
    --card-dark-edge: #2f2f2f;
    --backdrop: #e9e7e4;
    --white: #ffffff;
  }
  * { margin: 0; padding: 0; box-sizing: border-box; }
  html, body { width: 1200px; height: 960px; overflow: hidden; }
  body {
    background: var(--backdrop);
    font-family: "Roboto", Arial, sans-serif;
    position: relative;
  }
  .card {
    position: absolute;
    width: 600px;
    height: 342px;
    border-radius: 22px;
    overflow: hidden;
  }
  .card--front { left: 314px; top: 114px; background: var(--card-white); }
  .card--back {
    left: 312px; top: 473px;
    background: linear-gradient(135deg, var(--card-dark-edge), var(--card-dark));
  }
  .card__bands { position: absolute; left: 0; top: 0; }

  .brand { position: absolute; text-align: center; color: var(--brand-blue); }
  .brand__name {
    display: block;
    font-family: "Roboto", Arial, sans-serif;
    font-weight: 900;
    letter-spacing: 1px;
    line-height: 1;
  }
  .brand__descriptor { display: block; font-weight: 700; line-height: 1; }

  .card--front .brand { right: 36px; top: 72px; width: 232px; }
  .card--front .brand__name { font-size: 50px; }
  .card--front .brand__descriptor { font-size: 15px; margin-top: 8px; }

  .holder {
    position: absolute; left: 34px; top: 176px;
    font-family: "Roboto Condensed", "Arial Narrow", sans-serif;
    font-weight: 700; color: var(--brand-blue);
  }
  .holder__name { font-size: 21px; text-transform: uppercase; }
  .holder__credentials { font-size: 12px; margin-left: 4px; }
  .divider {
    position: absolute; left: 35px; top: 212px;
    width: 530px; height: 1px; background: var(--rule);
  }
  .contact-list {
    position: absolute; left: 34px; top: 227px;
    list-style: none; font-size: 14.5px; color: var(--ink);
  }
  .contact-list li { display: flex; align-items: center; height: 19px; }
  .contact-list svg { width: 14px; height: 14px; margin-right: 9px; fill: var(--brand-blue); }
  .address {
    position: absolute; right: 35px; top: 246px;
    text-align: right; font-size: 14.5px; line-height: 19px; color: var(--ink);
    font-style: normal;
  }
  .website {
    position: absolute; right: 30px; top: 313px;
    font-size: 14.5px; letter-spacing: 1.2px; color: var(--white);
  }

  .back-ornament {
    position: absolute; left: -120px; top: -40px;
    width: 300px; height: 300px; border-radius: 50%;
    background: #2e4a5a; opacity: 0.55;
  }
  .card--back .brand { left: 330px; top: 200px; width: 200px; }
  .card--back .brand__name { font-size: 42px; }
  .card--back .brand__descriptor { font-size: 12.5px; margin-top: 6px; }
  .tagline {
    position: absolute; left: 340px; top: 284px;
    font-style: italic; font-weight: 500; font-size: 15.5px; color: var(--white);
  }
</style>
</head>
<body>

<section class="card card--front" aria-label="Card front">
  <svg class="card__bands" width="600" height="342" viewBox="0 0 600 342" aria-hidden="true">
    <rect x="0" y="319" width="340" height="9" fill="var(--band-grey)"/>
    <rect x="0" y="328" width="600" height="14" fill="var(--brand-blue)"/>
    <path d="M330 342 Q338 342 341 332 L346 314 Q350 304 362 304 L600 304 L600 342 Z" fill="var(--brand-blue)" stroke="var(--white)" stroke-width="2"/>
  </svg>

  <div class="brand">
    <span class="brand__name">VALMIRA</span>
    <span class="brand__descriptor">Integrative Holistic Medicine</span>
  </div>

  <p class="holder">
    <span class="holder__name">Tobias Wrenfeld</span><span class="holder__credentials">- DOE, CPT, LMT</span>
  </p>
  <div class="divider"></div>

  <ul class="contact-list">
    <li>
      <svg viewBox="0 0 24 24" aria-hidden="true"><path d="M6.6 10.8a15.1 15.1 0 0 0 6.6 6.6l2.2-2.2c.3-.3.7-.4 1-.2 1.1.4 2.3.6 3.6.6.6 0 1 .4 1 1V20c0 .6-.4 1-1 1A17 17 0 0 1 3 4c0-.6.4-1 1-1h3.5c.6 0 1 .4 1 1 0 1.3.2 2.5.6 3.6.1.3 0 .7-.2 1z"/></svg>
      512 555 0148
    </li>
    <li>
      <svg viewBox="0 0 24 24" aria-hidden="true"><path d="M7 1h10a2 2 0 0 1 2 2v18a2 2 0 0 1-2 2H7a2 2 0 0 1-2-2V3a2 2 0 0 1 2-2zm0 3v15h10V4zm5 16.2a1 1 0 1 0 0 2 1 1 0 0 0 0-2z"/></svg>
      818 555 0192
    </li>
    <li>
      <svg viewBox="0 0 24 24" aria-hidden="true"><path d="M2 5h20v2l-10 6L2 7zm0 4.3 10 6 10-6V19H2z"/></svg>
      t.wrenfeld@ValmiraHealth.example
    </li>
  </ul>

  <address class="address">4100 East Marrow Drive<br>Austin, TX 78119</address>

  <p class="website">www.ValmiraHealth.example</p>
</section>

<section class="card card--back" aria-label="Card back">
  <div class="back-ornament"></div>
  <div class="brand">
    <span class="brand__name">VALMIRA</span>
    <span class="brand__descriptor">Integrative Holistic Medicine</span>
  </div>
  <p class="tagline">helping the body help itself</p>
</section>

</body>
</html>
```